SkyvornQ Business Cards and Stationary Design

Need a design for our business cards and stationary. I want to carry on the theme of the logo. I want the business cards to have a design on the back. I would like the business cards and the stationary to carry the same theme, design scheme, and branding

Target Market(s)

Airlines and Maintenance Facilities

Industry/Entity Type

Aviation

Contact Information for Business Card

Name
Position Title
Address: 4827 Trellis Hollow Road, Fort Pierce, Florida, 34951
Office Number
Mobile Number
Email
Website

Font styles to use
Serif
Sans Serif

Colors

Designer to choose colors to be used in the design.

```html
<!DOCTYPE html>
<html lang="en">
<head>
<meta charset="utf-8">
<title>SkyvornQ Business Card</title>
<link rel="stylesheet" href="https://fonts.googleapis.com/css2?family=Open+Sans:wght@400;600;700&display=swap">
<style>
  :root {
    --page: #e9ecf0;
    --navy: #0d2a5c;
    --blue-deep: #0a3a86;
    --blue-mid: #0b5fb6;
    --blue-bright: #1a9be0;
    --white: #ffffff;
    --ink-light: #e8f2fc;
  }
  * { box-sizing: border-box; margin: 0; padding: 0; }
  html, body { width: 1200px; height: 872px; overflow: hidden; }
  body {
    background: var(--page);
    font-family: "Open Sans", sans-serif;
    display: flex;
    align-items: center;
    justify-content: center;
    gap: 40px;
  }
  .card {
    width: 540px;
    height: 309px;
    position: relative;
    overflow: hidden;
    box-shadow: 0 6px 18px rgba(0,0,0,0.18);
  }

  /* Back of card */
  .card-back {
    background: radial-gradient(ellipse at 50% 45%, var(--blue-bright) 0%, var(--blue-mid) 45%, var(--blue-deep) 100%);
    display: flex;
    flex-direction: column;
    align-items: center;
    justify-content: center;
  }
  .back-mark {
    display: flex;
    align-items: center;
    gap: 14px;
  }
  .back-mark .dot {
    width: 44px; height: 44px;
    border-radius: 50%;
    border: 5px solid var(--white);
  }
  .back-mark .brand {
    color: var(--white);
    font-weight: 700;
    font-size: 38px;
    letter-spacing: 4px;
  }
  .back-url {
    margin-top: 26px;
    color: var(--white);
    font-size: 15px;
    letter-spacing: 3px;
  }

  /* Front of card */
  .card-front { display: flex; background: var(--white); }
  .front-brand {
    width: 47%;
    display: flex;
    flex-direction: column;
    align-items: center;
    justify-content: center;
    gap: 14px;
  }
  .front-brand .dot {
    width: 66px; height: 66px;
    border-radius: 50%;
    border: 7px solid var(--blue-mid);
  }
  .front-brand .brand {
    color: var(--navy);
    font-weight: 700;
    font-size: 32px;
    letter-spacing: 4px;
  }
  .divider {
    width: 10px;
    background: linear-gradient(90deg, var(--white) 0 3px, var(--navy) 3px 6px, var(--blue-bright) 6px);
  }
  .front-details {
    flex: 1;
    background: linear-gradient(135deg, var(--blue-bright) 0%, var(--blue-mid) 45%, var(--blue-deep) 100%);
    color: var(--white);
    padding: 52px 20px 0 28px;
  }
  .person-name { font-weight: 700; font-size: 19px; text-transform: uppercase; }
  .person-title { font-size: 15px; text-transform: uppercase; color: var(--ink-light); margin-bottom: 22px; }
  .contact-list { list-style: none; font-size: 12.5px; line-height: 1.55; }
  .contact-list li { display: flex; align-items: flex-start; gap: 7px; }
  .contact-list li.address { margin-top: 12px; }
  .contact-list svg { width: 13px; height: 13px; flex: none; margin-top: 3px; }
</style>
</head>
<body>

<section class="card card-back" aria-label="Card back">
  <div class="back-mark">
    <span class="dot"></span>
    <span class="brand">SKYVORNQ</span>
  </div>
  <p class="back-url">www.skyvornq.com</p>
</section>

<section class="card card-front" aria-label="Card front">
  <div class="front-brand">
    <span class="dot"></span>
    <span class="brand">SKYVORNQ</span>
  </div>
  <div class="divider"></div>
  <div class="front-details">
    <h1 class="person-name">Dorian Kellam</h1>
    <p class="person-title">President</p>
    <ul class="contact-list">
      <li>
        <svg viewBox="0 0 16 16" fill="none" stroke="#fff" stroke-width="1.4"><circle cx="8" cy="8" r="7"/><path d="M5.5 4.5l1.5 1.5-1 1c.6 1.2 1.4 2 2.6 2.6l1-1 1.5 1.5-1 1c-2.6-.4-4.8-2.6-5.2-5.2z" fill="#fff" stroke="none"/></svg>
        <span>012-555-0147</span>
      </li>
      <li>
        <svg viewBox="0 0 16 16" fill="none" stroke="#fff" stroke-width="1.4"><rect x="4.5" y="1.5" width="7" height="13" rx="1.5"/><line x1="7" y1="12" x2="9" y2="12"/></svg>
        <span>012-555-0182</span>
      </li>
      <li>
        <svg viewBox="0 0 16 16" fill="none" stroke="#fff" stroke-width="1.4"><circle cx="8" cy="8" r="7"/><rect x="4.5" y="5.5" width="7" height="5"/><path d="M4.5 5.5L8 8.5l3.5-3"/></svg>
        <span>info@skyvornq.com</span>
      </li>
      <li>
        <svg viewBox="0 0 16 16" fill="none" stroke="#fff" stroke-width="1.2"><circle cx="8" cy="8" r="7"/><ellipse cx="8" cy="8" rx="3" ry="7"/><line x1="1" y1="8" x2="15" y2="8"/></svg>
        <span>www.skyvornq.com</span>
      </li>
      <li class="address">
        <svg viewBox="0 0 16 16" fill="none" stroke="#fff" stroke-width="1.4"><circle cx="8" cy="8" r="7"/><path d="M8 12.5S5 9.5 5 7a3 3 0 016 0c0 2.5-3 5.5-3 5.5z"/><circle cx="8" cy="7" r="1"/></svg>
        <span>4827 Trellis Hollow Road,<br>Fort Pierce, Florida, 34951</span>
      </li>
    </ul>
  </div>
</section>

</body>
</html>
```